Easy - Fix our "Grab a Feast" Promo Flyer

Please see attached promo flyer with all the information required. Looking for quick assistance so we can go live with the advertising for this competition. Looking for something more commercial and polished. Very attractive so that lots of people enter the competition. <br/><br/>Happy for it to look a little bit festive as the competition is running in December. <br/><br/>Attached is out Grill Kammer Logo and first attempts at poster. Please let me know if you need anything further. <br/><br/>If you see any grammar or spelling errors please feel free to fix too.
Target Market(s)
Corporate Businesses who are buying vouchers as staff christmas gifts/bonus
Colors
Look and feel

```html
<!DOCTYPE html>
<html lang="en">
<head>
<meta charset="utf-8">
<title>Grill Kammer – Ultimate Staff Party Promo Flyer</title>
<link rel="stylesheet" href="https://fonts.googleapis.com/css2?family=Open+Sans:wght@400;600;700;800&display=swap">
<style>
  :root {
    --page-bg: #f2f0ef;
    --maroon-deep: #1c0504;
    --maroon: #5a0f0c;
    --red: #a81c17;
    --glow: #f3e6e4;
    --ink: #120403;
    --white: #ffffff;
    --brand-red: #d3201b;
    --voucher-kraft: #c9a673;
    --voucher-yellow: #f2c230;
    --voucher-red: #d8271f;
  }
  * { box-sizing: border-box; margin: 0; padding: 0; }
  html, body { width: 1200px; height: 1200px; overflow: hidden; }
  body {
    background: var(--page-bg);
    font-family: "Open Sans", sans-serif;
    display: flex; align-items: center; justify-content: center;
  }
  .flyer {
    position: relative;
    width: 806px; height: 1140px;
    overflow: hidden;
    color: var(--white);
    background:
      radial-gradient(ellipse 330px 330px at 50% 50%, var(--glow) 0%, rgba(220,150,145,.85) 30%, rgba(168,28,23,0) 75%),
      radial-gradient(ellipse 620px 700px at 50% 42%, var(--red) 0%, var(--maroon) 55%, var(--maroon-deep) 100%);
    box-shadow: 0 10px 40px rgba(0,0,0,.25);
  }
  .flyer__bokeh {
    position: absolute; inset: 0 0 auto 0; height: 520px;
    background:
      radial-gradient(circle at 20% 30%, rgba(230,60,40,.35), transparent 18%),
      radial-gradient(circle at 80% 40%, rgba(240,120,40,.3), transparent 16%),
      radial-gradient(circle at 60% 15%, rgba(240,80,40,.25), transparent 14%);
  }
  .brand-tag {
    position: absolute; top: 26px; right: 60px;
    width: 128px; height: 104px;
    background: var(--white);
    outline: 2px dashed var(--white); outline-offset: 4px;
    display: flex; align-items: center; justify-content: center; gap: 6px;
  }
  .brand-tag__dot { width: 12px; height: 12px; border-radius: 50%; background: var(--brand-red); }
  .brand-tag__name {
    color: var(--brand-red); font-weight: 800; font-size: 17px; line-height: 1.05; text-align: center;
  }
  .kicker {
    position: absolute; top: 74px; left: 205px; width: 404px;
    text-align: center; font-weight: 800; font-size: 30px; letter-spacing: -0.5px;
    padding: 8px 0;
    border-top: 2px dotted rgba(255,255,255,.8);
    border-bottom: 2px dotted rgba(255,255,255,.8);
  }
  .headline {
    position: absolute; top: 150px; left: 0; right: 0; text-align: center;
    text-shadow: 0 0 18px rgba(255,255,255,.55);
    line-height: .9;
  }
  .headline__staff { display: block; font-weight: 400; font-size: 170px; letter-spacing: -4px; }
  .headline__party { display: block; font-weight: 800; font-size: 176px; letter-spacing: -6px; margin-top: 4px; }
  .headline__sub {
    position: absolute; top: 452px; right: 140px;
    color: var(--ink); font-weight: 700; font-size: 15px;
  }
  .offer { position: absolute; top: 510px; left: 0; right: 0; text-align: center; color: var(--ink); }
  .offer__lead { font-weight: 700; font-size: 21px; }
  .offer__date { font-weight: 800; font-size: 64px; letter-spacing: -2px; line-height: 1.05; }
  .offer__date sup { font-size: 24px; vertical-align: 30px; letter-spacing: 0; }
  .draw { position: absolute; top: 640px; left: 0; right: 0; text-align: center; }
  .draw__lead { font-size: 16px; font-weight: 600; color: #f4d6d2; }
  .draw__row { display: flex; align-items: center; justify-content: center; gap: 14px; }
  .draw__rule { width: 120px; height: 7px; border-top: 2px solid var(--ink); border-bottom: 2px solid var(--ink); }
  .draw__title { font-weight: 800; font-size: 27px; color: #f7e4e1; }
  .draw__for { font-size: 15px; font-weight: 700; margin-top: -4px; }
  .details { position: absolute; top: 745px; left: 0; right: 0; text-align: center; font-weight: 700; }
  .details p { font-size: 14.5px; line-height: 1.45; }
  .details .details__cake { font-size: 19px; margin-top: 4px; }
  .vouchers {
    position: absolute; top: 852px; left: 60px; right: 60px;
    display: flex; justify-content: space-between;
  }
  .voucher { width: 196px; height: 64px; border: 2px solid var(--white); }
  .voucher--kraft { background: linear-gradient(180deg, #d8b887, var(--voucher-kraft)); }
  .voucher--yellow { background: linear-gradient(180deg, #f7d45a, var(--voucher-yellow)); }
  .voucher--red { background: linear-gradient(180deg, #e5453d, var(--voucher-red)); }
  .closing { position: absolute; top: 940px; left: 0; right: 0; text-align: center; }
  .closing__title { font-weight: 800; font-size: 29px; letter-spacing: -0.5px; }
  .closing__tip { font-weight: 700; font-size: 13px; margin-top: 4px; }
  .closing__note { font-weight: 700; font-size: 13px; }
  .closing__terms { font-size: 9px; font-weight: 700; margin-top: 2px; }
  .contact {
    position: absolute; top: 1045px; left: 70px; right: 40px;
    display: flex; align-items: center; gap: 36px;
  }
  .contact__label { font-weight: 800; font-size: 20px; }
  .contact__phone { display: flex; align-items: center; gap: 10px; font-weight: 800; font-size: 44px; letter-spacing: -1px; }
  .contact__links { display: flex; flex-direction: column; gap: 10px; font-weight: 700; font-size: 16px; }
  .contact__link { display: flex; align-items: center; gap: 8px; }
  .icon { flex: none; }
</style>
</head>
<body>
  <article class="flyer">
    <div class="flyer__bokeh" role="img" aria-label="Soft festive bokeh lights in red and gold"></div>

    <div class="brand-tag">
      <span class="brand-tag__dot"></span>
      <span class="brand-tag__name">GRILL<br>KAMMER</span>
    </div>

    <div class="kicker">WIN THE ULTIMATE</div>

    <h1 class="headline">
      <span class="headline__staff">STAFF</span>
      <span class="headline__party">PARTY</span>
    </h1>
    <div class="headline__sub">FOR YOU AND YOUR COLLEAGUES</div>

    <section class="offer">
      <p class="offer__lead">Purchase K5,000 worth of vouchers before</p>
      <p class="offer__date">DECEMBER 31<sup>st</sup></p>
    </section>

    <section class="draw">
      <p class="draw__lead">And go into the draw to WIN the</p>
      <div class="draw__row">
        <span class="draw__rule"></span>
        <span class="draw__title">ULTIMATE STAFF PARTY</span>
        <span class="draw__rule"></span>
      </div>
      <p class="draw__for">for 150 people.</p>
    </section>

    <section class="details">
      <p>This includes a Venue, BBQ Style PNG Menu, Roast Pork, Decor &amp; much more...</p>
      <p>So HURRY! There are ONLY 2 parties to WIN!!!</p>
      <p class="details__cake">We will even throw in an extra large themed cake with your company logo on it.</p>
    </section>

    <div class="vouchers">
      <div class="voucher voucher--kraft" role="img" aria-label="Kraft paper shopping voucher, K100"></div>
      <div class="voucher voucher--yellow" role="img" aria-label="Yellow shopping voucher, K100"></div>
      <div class="voucher voucher--red" role="img" aria-label="Red shopping voucher, K100"></div>
    </div>

    <section class="closing">
      <h2 class="closing__title">Have a MIGHTY XMAS at GRILL KAMMER</h2>
      <p class="closing__tip">TIP: BUY MORE VOUCHERS TO HAVE BETTER CHANCES OF WINNING</p>
      <p class="closing__note">“For every HR department enquiry we receive, a special surprise will be given. So HURRY UP!</p>
      <p class="closing__terms">TERMS &amp; CONDITIONS APPLY</p>
    </section>

    <footer class="contact">
      <span class="contact__label">Contact us</span>
      <span class="contact__phone">
        <svg class="icon" width="34" height="34" viewBox="0 0 34 34" aria-hidden="true">
          <circle cx="17" cy="17" r="15" fill="none" stroke="#fff" stroke-width="2.5"/>
          <path d="M11 10c1-1 2.5-1 3 0l1.5 3c.4.8 0 1.5-.7 2l-1 .8c.9 2 2.4 3.5 4.4 4.4l.8-1c.5-.7 1.2-1.1 2-.7l3 1.5c1 .5 1 2 0 3-1.5 1.5-4 2-7-.2-2.5-1.8-4.4-3.7-6-6.2C9.3 14 9.6 11.5 11 10z" fill="#fff"/>
        </svg>
        7555 0142
      </span>
      <div class="contact__links">
        <span class="contact__link">
          <svg class="icon" width="24" height="24" viewBox="0 0 24 24" aria-hidden="true">
            <circle cx="12" cy="12" r="11" fill="none" stroke="#fff" stroke-width="2"/>
            <rect x="6" y="8" width="12" height="8" fill="#fff"/>
            <path d="M6 8l6 5 6-5" fill="none" stroke="#5a0f0c" stroke-width="1.4"/>
          </svg>
          sales@grillkammer-png.com
        </span>
        <span class="contact__link">
          <svg class="icon" width="24" height="24" viewBox="0 0 24 24" aria-hidden="true">
            <circle cx="12" cy="12" r="11" fill="none" stroke="#fff" stroke-width="2"/>
          </svg>
          grillkammerpng
        </span>
      </div>
    </footer>
  </article>
</body>
</html>
```